Kelbrook Plumbing flyer

I want to incorporate our logo design into a new flyer promoting the business and advertising products that we install.
We install hot water systems, Air-conditioning systems and central heating systems. Along with other aspects of plumbing such as gasfitting, roofing, sanitary and drainage
I would like the background to be the same as our business cards with the water effect and colours.

Requirements
Must have
• Logo
24/7 Emergency call out
Aspects of plumbing we do
- Hot water systems
- Central Heating
- Solar hot water systems/ heat pump systems
- Gasfitting
- Drainage
- Roofing
- Air-Conditioning
Nice to have
• Pictures of hot water systems and air-conditioning system
$30 off voucher when producing this flyer (limit 1 per house hold)

```html
<!DOCTYPE html>
<html lang="en">
<head>
<meta charset="utf-8">
<title>Kelbrook Plumbing Flyer</title>
<link rel="stylesheet" href="https://fonts.googleapis.com/css2?family=Exo+2:wght@700;800&family=Roboto:wght@400;700&family=Roboto+Condensed:wght@300;400;700&display=swap">
<style>
:root{
  --ink-dark:#222325;
  --ink-darker:#18191b;
  --blue:#1597dc;
  --blue-deep:#0b6fb8;
  --white:#ffffff;
  --text:#2b2b2b;
  --paper:#f3f5f7;
  --band:#e6e9ec;
  --silver:#d4d6d8;
  --gold:#e7b324;
}
*{margin:0;padding:0;box-sizing:border-box}
html,body{width:891px;height:1200px;overflow:hidden;background:var(--ink-darker)}
.flyer{position:relative;width:891px;height:1200px;overflow:hidden;background:var(--paper);font-family:"Roboto Condensed",sans-serif}
.hero{position:absolute;left:0;top:0;width:891px;height:440px;background:radial-gradient(circle at 30% 40%,#2c2d30,var(--ink-dark) 70%)}
.brand{position:absolute;left:44px;top:78px;display:flex;align-items:center;gap:14px}
.brand-dot{width:58px;height:58px;border-radius:50%;background:var(--blue)}
.brand-name{font-family:"Exo 2",sans-serif;font-weight:800;font-size:34px;line-height:1;color:var(--blue);letter-spacing:.5px}
.hero-kicker{position:absolute;left:44px;top:192px;color:var(--white);font-weight:300;font-size:33px;line-height:1;letter-spacing:-.5px}
.hero-title{position:absolute;left:40px;top:239px;font-family:"Exo 2",sans-serif;font-weight:800;font-size:64px;line-height:55px;color:var(--blue);letter-spacing:-1px}
.hero-frame{position:absolute;left:390px;top:-40px;width:560px;height:560px}
.work-photos{position:absolute;left:0;top:442px;width:735px;height:192px}
.emergency{position:absolute;left:556px;top:350px;width:300px;height:300px}
.aspects{position:absolute;left:54px;top:661px}
.aspects h2{font-size:28px;font-weight:700;color:var(--text);letter-spacing:-.3px;line-height:34px}
.aspects h2 span{color:var(--blue)}
.service-list{position:absolute;left:26px;top:716px;width:380px;list-style:none}
.service-list li{display:flex;align-items:center;gap:14px;padding:0 0 0 28px;height:30px;margin-bottom:11px;font-size:24px;color:var(--text);line-height:25px}
.service-list li:nth-child(odd){background:linear-gradient(90deg,var(--band),rgba(230,233,236,0))}
.service-list li.two-line{height:52px}
.service-icon{flex:0 0 24px;width:24px;height:24px;border-radius:50%;background:var(--blue)}
.divider{position:absolute;left:429px;top:660px;width:1px;height:355px;background:#d6d9dc}
.install{position:absolute;left:470px;top:683px;width:400px}
.install h3{font-size:23px;font-weight:700;color:var(--blue);line-height:27px}
.install p{margin-top:6px;font-size:19px;color:var(--text);line-height:21px}
.products{position:absolute;left:480px;top:831px;width:356px;height:178px;border-radius:4px;background:linear-gradient(180deg,#f7f7f5,#dcdcd8)}
.voucher{position:absolute;left:0;top:1040px;width:891px;height:66px}
.voucher-text{position:absolute;left:44px;top:1055px;color:var(--white);font-weight:700;font-size:29px;line-height:34px;letter-spacing:-.3px}
.voucher-text small{font-weight:400;font-size:19px}
.contact{position:absolute;left:0;top:1100px;width:891px;height:100px;background:radial-gradient(circle at 40% 30%,#2c2d30,var(--ink-darker) 80%)}
.contact-phone-icon{position:absolute;left:34px;top:1116px}
.contact-name{position:absolute;left:108px;top:1112px;font-family:"Exo 2",sans-serif;font-weight:800;font-size:40px;line-height:40px;color:var(--blue);letter-spacing:1px}
.contact-number{position:absolute;left:108px;top:1148px;font-family:"Exo 2",sans-serif;font-weight:700;font-size:40px;line-height:40px;color:var(--white);letter-spacing:.5px}
.contact-line{position:absolute;left:405px;display:flex;align-items:center;gap:9px;color:var(--white);font-family:"Roboto",sans-serif;font-size:20px;line-height:22px}
.contact-line.email{top:1123px}
.contact-line.web{top:1154px}
.seal{position:absolute;left:716px;top:1021px;width:134px;height:134px;border-radius:50%;background:var(--gold)}
.licence{position:absolute;left:737px;top:1163px;color:var(--white);font-size:14px}
</style>
</head>
<body>
<main class="flyer">
  <section class="hero">
    <div class="brand"><span class="brand-dot"></span><span class="brand-name">KELBROOK<br>PLUMBING</span></div>
    <p class="hero-kicker">NEED A PROFESSIONAL</p>
    <h1 class="hero-title">EXPERT<br>PLUMBING<br>SERVICES?</h1>
  </section>

  <svg class="hero-frame" viewBox="0 0 560 560">
    <defs><linearGradient id="heroPhoto" x1="0" y1="0" x2="1" y2="1"><stop offset="0" stop-color="#3e5f96"/><stop offset=".55" stop-color="#2d4a7c"/><stop offset="1" stop-color="#d9702c"/></linearGradient></defs>
    <circle cx="280" cy="280" r="256" fill="var(--silver)"/>
    <circle cx="280" cy="280" r="236" fill="#ffffff"/>
    <circle cx="280" cy="280" r="228" fill="url(#heroPhoto)" role="img" aria-label="Plumber in blue work shirt holding hoses with an orange tool bag"/>
  </svg>

  <svg class="work-photos" viewBox="0 0 735 192" role="img" aria-label="Site photos of trenching, pipework and installed hot water units on brick walls">
    <defs>
      <linearGradient id="soil" x1="0" y1="0" x2="1" y2="1"><stop offset="0" stop-color="#a98a63"/><stop offset="1" stop-color="#7a5c3c"/></linearGradient>
      <linearGradient id="brick" x1="0" y1="0" x2="1" y2="1"><stop offset="0" stop-color="#c9c4bc"/><stop offset=".4" stop-color="#a8644b"/><stop offset="1" stop-color="#8c4f3a"/></linearGradient>
    </defs>
    <path d="M0 0H318Q312 0 308 10L266 180Q262 192 250 192H0Z" fill="url(#soil)"/>
    <path d="M348 0H735V192H282Q272 192 276 180L320 12Q324 0 348 0Z" fill="url(#brick)"/>
  </svg>

  <svg class="emergency" viewBox="0 0 300 300">
    <defs><linearGradient id="ring" x1="0" y1="0" x2="0" y2="1"><stop offset="0" stop-color="#f2f2f2"/><stop offset="1" stop-color="#b9bcbf"/></linearGradient>
      <linearGradient id="digits" x1="0" y1="0" x2="0" y2="1"><stop offset="0" stop-color="#ffffff"/><stop offset="1" stop-color="#c9ccd0"/></linearGradient>
      <clipPath id="inner"><circle cx="150" cy="150" r="132"/></clipPath></defs>
    <circle cx="150" cy="150" r="148" fill="url(#ring)"/>
    <circle cx="150" cy="150" r="132" fill="var(--blue)"/>
    <rect x="0" y="168" width="300" height="80" fill="var(--ink-dark)" clip-path="url(#inner)"/>
    <text x="150" y="156" text-anchor="middle" font-family="Roboto Condensed, sans-serif" font-weight="700" font-size="92" fill="url(#digits)">24/7</text>
    <text x="150" y="200" text-anchor="middle" font-family="Roboto, sans-serif" font-weight="700" font-size="26" fill="#fff">EMERGENCY</text>
    <text x="150" y="232" text-anchor="middle" font-family="Roboto, sans-serif" font-weight="700" font-size="30" fill="#fff">CALL OUT</text>
  </svg>

  <section class="aspects"><h2><span>Aspects of</span> Plumbing we do:</h2></section>
  <ul class="service-list">
    <li><span class="service-icon"></span>Hot water systems</li>
    <li><span class="service-icon"></span>Central Heating</li>
    <li class="two-line"><span class="service-icon"></span>Solar hot water systems /<br>Heat pump systems</li>
    <li><span class="service-icon"></span>Gasfitting</li>
    <li><span class="service-icon"></span>Drainage</li>
    <li><span class="service-icon"></span>Roofing</li>
    <li><span class="service-icon"></span>Air-Conditioning</li>
  </ul>

  <div class="divider"></div>
  <section class="install">
    <h3>We install hot water systems,<br>Air-conditioning systems &amp; central<br>heating systems.</h3>
    <p>Along with other aspects of plumbing such as<br>gasfitting, roofing, sanitary and drainage</p>
  </section>
  <div class="products" role="img" aria-label="Heat pump hot water tank with outdoor unit, electric storage heaters and a gas continuous flow unit"></div>

  <svg class="voucher" viewBox="0 0 891 66" preserveAspectRatio="none" aria-hidden="true">
    <path d="M0 8 Q11 0 22 8 T44 8 T66 8 T88 8 T110 8 T132 8 T154 8 T176 8 T198 8 T220 8 T242 8 T264 8 T286 8 T308 8 T330 8 T352 8 T374 8 T396 8 T418 8 T440 8 T462 8 T484 8 T506 8 T528 8 T550 8 T572 8 T594 8 T616 8 T638 8 T660 8 T682 8 T704 8 T726 8 T748 8 T770 8 T792 8 T814 8 T836 8 T858 8 T880 8 T902 8 V66 H0Z" fill="var(--blue-deep)"/>
  </svg>
  <p class="voucher-text">$30 off voucher when producing this flyer <small>(limit 1 per house hold)</small></p>

  <footer class="contact"></footer>
  <svg class="contact-phone-icon" width="50" height="58" viewBox="0 0 50 58" aria-hidden="true">
    <rect x="12" y="2" width="28" height="50" rx="5" fill="none" stroke="var(--blue)" stroke-width="4"/>
    <circle cx="26" cy="45" r="2.5" fill="var(--blue)"/>
    <path d="M2 30 Q2 56 26 56 L14 56 Q0 50 2 30Z" fill="var(--blue)"/>
  </svg>
  <p class="contact-name">DAN MERCER</p>
  <p class="contact-number">0412 587 930</p>
  <p class="contact-line email"><svg width="18" height="18" viewBox="0 0 16 16"><circle cx="8" cy="8" r="8" fill="var(--blue)"/><rect x="4" y="5" width="8" height="6" fill="none" stroke="#fff" stroke-width="1.2"/><path d="M4 5 8 8.5 12 5" fill="none" stroke="#fff" stroke-width="1.2"/></svg>dan@kelbrookplumbing.com</p>
  <p class="contact-line web"><svg width="18" height="18" viewBox="0 0 16 16"><circle cx="8" cy="8" r="7" fill="none" stroke="var(--blue)" stroke-width="1.6"/><ellipse cx="8" cy="8" rx="3" ry="7" fill="none" stroke="var(--blue)" stroke-width="1.3"/><path d="M1 8H15" stroke="var(--blue)" stroke-width="1.3"/></svg>www.kelbrookplumbing.com</p>
  <div class="seal" aria-hidden="true"></div>
  <p class="licence">Lic. No. 208417</p>
</main>
</body>
</html>
```